"Cedar Hollow Realty" is the name of my real estate company

This is for a: "for sale" sign, looking for a minimalist design, wire frame outline of a midcentury modern homes roof line or elevation?

My name is: Dean Marlowe (needed)
My Cell # is: 415 208 3947 (needed)
My BRE license # is: 02468135 (needed)
BRE needs to be displayed in this format: BRE 02468135 (needed)
The white outline on the sign riders 'pictured" may work on large sign
Note font on pictured rider sign

This design is for a real estate "for sale" sign or sandwich board sign. Do Not include the words "For Sale" on the sign.

The measurements are 36" inches (91.44 cm) Length, or tall X 24" inches (60.90 cm) Wide.

|
3
---- 24 ----
6
|

Sorry I wasn't more specific earlier. I'd like the elements of the sign to be scaled in size according to their importance, from largest to smallest:

My name: Dean Marlowe
My phone number: 415-208-3947
My company name: Cedar Hollow Realty
My license number: BRE 02468135 (This can be much smaller than the smallest text)
Additionally, please incorporate contemporary to mid-century modern elements on the wire frame roofline or a simple roof-like design.

Thank you!

Best regards,
Dean

```html
<!DOCTYPE html>
<html lang="en">
<head>
<meta charset="utf-8">
<title>Dean Marlowe – Real Estate Sign</title>
<link href="https://fonts.googleapis.com/css2?family=Montserrat:wght@300;400;600;700&display=swap" rel="stylesheet">
<style>
  :root {
    --sign-bg: #000000;
    --sign-ink: #ffffff;
  }
  html, body {
    margin: 0;
    padding: 0;
    width: 1200px;
    height: 1200px;
    overflow: hidden;
    background: var(--sign-bg);
  }
  .canvas {
    position: relative;
    width: 1200px;
    height: 1200px;
    background: var(--sign-bg);
    font-family: "Montserrat", sans-serif;
    color: var(--sign-ink);
  }
  .sign-frame {
    position: absolute;
    left: 248px;
    top: 80px;
    width: 704px;
    height: 1040px;
    box-sizing: border-box;
    border: 3px solid var(--sign-ink);
  }
  .sign-frame > * {
    position: absolute;
    left: 0;
    right: 0;
    margin: 0;
    text-align: center;
  }
  .company-name {
    top: 108px;
    font-size: 30px;
    font-weight: 700;
    letter-spacing: -0.5px;
  }
  .brand-square {
    left: 264px;
    right: auto;
    top: 286px;
    width: 174px;
    height: 219px;
    background: var(--sign-ink);
  }
  .agent-name {
    top: 530px;
    font-size: 68px;
    font-weight: 400;
    line-height: 1;
    letter-spacing: 0;
    white-space: nowrap;
  }
  .agent-title {
    top: 602px;
    font-size: 21px;
    font-weight: 400;
    letter-spacing: 12px;
    padding-left: 12px;
  }
  .divider {
    left: 273px;
    right: auto;
    width: 157px;
    height: 3px;
    background: var(--sign-ink);
  }
  .divider--top { top: 732px; }
  .divider--bottom { top: 884px; }
  .call-to-action {
    top: 764px;
    font-size: 30px;
    font-weight: 700;
    letter-spacing: -0.5px;
  }
  .phone-number {
    top: 793px;
    font-size: 64px;
    font-weight: 700;
    letter-spacing: -1px;
  }
  .license-number {
    top: 985px;
    font-size: 20px;
    font-weight: 600;
    letter-spacing: 1.5px;
  }
</style>
</head>
<body>
  <div class="canvas">
    <section class="sign-frame">
      <p class="company-name">CEDAR HOLLOW REALTY</p>
      <div class="brand-square" aria-hidden="true"></div>
      <h1 class="agent-name">DEAN MARLOWE</h1>
      <p class="agent-title">REAL ESTATE AGENT</p>
      <div class="divider divider--top"></div>
      <p class="call-to-action">BOOK NOW</p>
      <p class="phone-number">415-208-3947</p>
      <div class="divider divider--bottom"></div>
      <p class="license-number">BRE 02468135</p>
    </section>
  </div>
</body>
</html>
```